Harrow Grading LLC business card design

Excavation company business cards

Contact Information for Business Card

Harrow Grading LLC cell phone 208-417-6290 office phone 208-319-4856 harrowgradingllc@maplecove.com Driveways, site prep, retaining walls, septic systems, rock delivery

Colors

Designer to choose colors to be used in the design.

```html
<!DOCTYPE html>
<html lang="en">
<head>
<meta charset="utf-8">
<title>Harrow Grading LLC — Business Card</title>
<link rel="stylesheet" href="https://fonts.googleapis.com/css2?family=Russo+One&family=Work+Sans:wght@400;500&display=swap">
<style>
  :root {
    --orange: #e8620f;
    --orange-soft: #f08a45;
    --white: #ffffff;
    --ink: #3a3a3a;
    --slate: #555555;
    --slate-dark: #3f3f3f;
    --backdrop: #d9d9d9;
  }
  * { margin: 0; padding: 0; box-sizing: border-box; }
  html, body { width: 1200px; height: 800px; overflow: hidden; }
  body {
    background: var(--backdrop);
    position: relative;
    font-family: "Work Sans", sans-serif;
  }
  .card {
    position: absolute;
    border-radius: 22px;
    overflow: hidden;
    box-shadow: 0 10px 28px rgba(0,0,0,0.18);
  }

  /* Front (vertical) */
  .card-front {
    left: 130px; top: 110px;
    width: 330px; height: 580px;
    background: var(--white);
  }
  .front-band { position: absolute; inset: 0; }
  .front-wordmark {
    position: absolute;
    top: 56px; left: 0; right: 0;
    text-align: center;
    font-family: "Russo One", sans-serif;
    color: var(--white);
    font-size: 25px;
    line-height: 1.2;
    letter-spacing: 1px;
  }
  .front-illustration {
    position: absolute;
    left: 60px; top: 150px;
    width: 210px; height: 160px;
    border-radius: 8px;
    background: linear-gradient(160deg, var(--orange-soft) 0%, #b94a0a 100%);
  }
  .person {
    position: absolute;
    top: 340px; left: 30px; right: 30px;
    text-align: center;
  }
  .person-name {
    font-family: "Russo One", sans-serif;
    color: var(--orange);
    font-size: 26px;
    letter-spacing: 1px;
    line-height: 1.2;
  }
  .person-rule {
    display: flex;
    align-items: center;
    gap: 8px;
    margin-top: 6px;
    color: var(--ink);
    font-size: 13px;
  }
  .person-rule::before, .person-rule::after {
    content: "";
    flex: 1;
    height: 1.5px;
    background: var(--orange);
  }
  .contact-icons {
    position: absolute;
    top: 412px; left: 0; right: 0;
    display: flex;
    justify-content: center;
    gap: 8px;
  }
  .contact-icon { width: 24px; height: 24px; display: block; }
  .contact-lines {
    position: absolute;
    top: 450px; left: 20px; right: 20px;
    list-style: none;
    color: var(--ink);
    text-align: center;
  }
  .contact-lines li { line-height: 22px; font-size: 16px; }
  .contact-lines li.small { font-size: 14px; }

  /* Back (horizontal) */
  .card-back {
    left: 540px; top: 250px;
    width: 580px; height: 330px;
    background: linear-gradient(135deg, var(--slate) 0%, var(--slate-dark) 100%);
  }
  .back-illustration {
    position: absolute;
    left: 170px; top: 50px;
    width: 240px; height: 130px;
    border-radius: 8px;
    background: linear-gradient(135deg, var(--orange) 0%, #3a3a3a 100%);
  }
  .back-wordmark {
    position: absolute;
    left: 0; right: 0; top: 196px;
    text-align: center;
    font-family: "Russo One", sans-serif;
    color: var(--orange);
    font-size: 40px;
    letter-spacing: 2px;
  }
</style>
</head>
<body>

  <section class="card card-front" aria-label="Business card front">
    <svg class="front-band" width="330" height="580" viewBox="0 0 330 580" aria-hidden="true">
      <polygon points="0,0 330,0 330,380 0,200" fill="var(--orange)"/>
    </svg>
    <div class="front-wordmark">HARROW GRADING<br>LLC</div>
    <div class="front-illustration" role="img" aria-label="Illustration of an excavator digging on a mountain ridge"></div>

    <div class="person">
      <div class="person-name">DANIEL REYES</div>
      <div class="person-rule">President</div>
    </div>

    <div class="contact-icons">
      <svg class="contact-icon" viewBox="0 0 22 22" aria-label="Office phone">
        <circle cx="11" cy="11" r="11" fill="var(--orange)"/>
        <path d="M7 6.5c.6-.6 1.4-.5 1.8.1l1 1.5c.3.5.2 1-.2 1.4l-.6.5c.6 1.3 1.6 2.3 2.9 2.9l.5-.6c.4-.4.9-.5 1.4-.2l1.5 1c.6.4.7 1.2.1 1.8-1.2 1.2-3 1.2-5.2-.6-1.9-1.6-3.6-3.7-3.4-6z" fill="var(--white)"/>
      </svg>
      <svg class="contact-icon" viewBox="0 0 22 22" aria-label="Cell phone">
        <circle cx="11" cy="11" r="11" fill="var(--orange)"/>
        <rect x="7.5" y="5" width="7" height="12" rx="1.2" fill="none" stroke="var(--white)" stroke-width="1.4"/>
        <circle cx="11" cy="15" r="0.8" fill="var(--white)"/>
      </svg>
      <svg class="contact-icon" viewBox="0 0 22 22" aria-label="Email">
        <circle cx="11" cy="11" r="11" fill="var(--orange)"/>
        <rect x="5.5" y="7" width="11" height="8" rx="1" fill="var(--white)"/>
        <path d="M5.8 7.5L11 11.5l5.2-4" fill="none" stroke="var(--orange)" stroke-width="1.1"/>
      </svg>
      <svg class="contact-icon" viewBox="0 0 22 22" aria-label="Website">
        <circle cx="11" cy="11" r="11" fill="var(--orange)"/>
        <circle cx="11" cy="11" r="5.5" fill="none" stroke="var(--white)" stroke-width="1.3"/>
        <ellipse cx="11" cy="11" rx="2.3" ry="5.5" fill="none" stroke="var(--white)" stroke-width="1.1"/>
        <line x1="5.5" y1="11" x2="16.5" y2="11" stroke="var(--white)" stroke-width="1.1"/>
      </svg>
    </div>
    <ul class="contact-lines">
      <li>208-319-4856</li>
      <li>208-417-6290</li>
      <li class="small">harrowgradingllc@maplecove.com</li>
      <li class="small">harrowgradingllc.com</li>
    </ul>
  </section>

  <section class="card card-back" aria-label="Business card back">
    <div class="back-illustration" role="img" aria-label="Illustration of an excavator in front of mountain peaks"></div>
    <div class="back-wordmark">HARROW GRADING LLC</div>
  </section>

</body>
</html>
```